Shopping centre customer engagement software website

We need a multi page site with :

*What we do.
*How it works.
*Benefits
* Case study
* Testimonial
* Business login (we provide link to business portal)
* Consumer login (we provide link to consumer site)
* Book a demo
* Contact us

We want it to be clean and crisp and very self explanatory with little clutter. We are thinking white but are open to what ever looks the best.
Updates

Wordpress is preferred

Need extra days to review

Target Market(s)

Shopping centre managers and retail property companies

Coding

Coded - Design and coding required

Number of Pages Required

5+ page

Font styles to use
Sans Serif

Colors
ffffff

Requirements
Must have
• As listed above and must be responsive! Checkout our existing site for the text to be included (will be edited but it’ll give you an idea) www.vostrelink.com

```html
<!DOCTYPE html>
<html lang="en">
<head>
<meta charset="utf-8">
<title>Vostrelink – Shopping Centre Engagement</title>
<link href="https://fonts.googleapis.com/css2?family=Arimo:wght@400;700&display=swap" rel="stylesheet">
<style>
:root{
  --white:#ffffff;
  --ink:#1f1f1f;
  --muted:#6d6d6d;
  --line:#e2e2e2;
  --band:#f3f3f3;
  --cyan:#5fd4ee;
  --cyan-soft:#8fdbee;
  --cyan-ink:#4bbfdc;
  --icon:#9aa7b3;
  --hero-light:#8fa1b6;
  --hero-mid:#66768a;
  --hero-dark:#4a5564;
}
*{box-sizing:border-box;margin:0;padding:0}
html,body{width:1200px;height:676px;overflow:hidden;background:var(--white)}
body{font-family:"Arimo",Arial,sans-serif;color:var(--ink)}
.page{width:1200px;height:676px;position:relative;background:var(--white)}

.site-header{height:68px;display:flex;align-items:center;padding:0 46px 0 48px;border-top:3px solid var(--cyan-soft)}
.brand{display:flex;align-items:center;gap:14px;width:300px}
.brand-dot{width:40px;height:40px;border-radius:50%;background:#9aa3ad}
.brand-name{font-size:24px;font-weight:400;letter-spacing:3px;color:var(--ink)}
.main-nav{display:flex;gap:30px;margin-left:60px}
.main-nav a{font-size:12.5px;color:var(--ink);text-decoration:none;letter-spacing:.2px}
.account-links{margin-left:auto;display:flex;gap:8px}
.btn-pill{display:inline-block;height:30px;line-height:28px;padding:0 18px;border-radius:15px;font-size:12px;text-decoration:none;border:1px solid var(--cyan-soft)}
.btn-outline{color:var(--cyan-ink);background:var(--white)}
.btn-filled{color:var(--white);background:var(--cyan-soft)}

.hero{position:relative;height:430px;
  background:linear-gradient(100deg,var(--hero-light) 0%,var(--hero-mid) 55%,var(--hero-dark) 100%)}
.hero-callout{position:absolute;left:278px;top:40px;background:var(--cyan);color:var(--white);font-size:18px;padding:13px 14px;}
.hero-callout::after{content:"";position:absolute;left:74px;bottom:-9px;border-left:8px solid transparent;border-right:8px solid transparent;border-top:9px solid var(--cyan)}

.sub-nav{height:30px;background:var(--band);border-bottom:1px solid var(--line);display:flex;align-items:center;padding:0 44px 0 84px;font-size:12px;color:var(--muted)}
.sub-nav .label{color:#555;margin-right:12px}
.sub-nav a{color:var(--muted);text-decoration:none;margin-right:22px}
.social{margin-left:auto;display:flex;align-items:center;gap:20px}
.social-square{width:14px;height:14px;background:var(--icon);border-radius:2px}

.intro{text-align:center;padding-top:18px}
.intro-title{font-size:18.5px;font-weight:400;line-height:25px;color:var(--ink)}
.intro-sub{font-size:11px;color:#444;margin-top:9px}
.btn-demo{display:inline-flex;align-items:center;gap:8px;margin-top:14px;height:34px;padding:0 17px;border:1px solid var(--cyan-soft);border-radius:17px;color:var(--cyan-ink);font-size:12px;font-weight:700;text-decoration:none;letter-spacing:.3px}
</style>
</head>
<body>
<div class="page">
  <header class="site-header">
    <div class="brand"><span class="brand-dot"></span><span class="brand-name">VOSTRELINK</span></div>
    <nav class="main-nav">
      <a href="#">HOW IT WORKS</a><a href="#">BENEFITS</a><a href="#">WHAT WE DO</a><a href="#">CASE STUDY</a>
    </nav>
    <div class="account-links">
      <a class="btn-pill btn-outline" href="#">Consumer login</a>
      <a class="btn-pill btn-filled" href="#">Business login</a>
    </div>
  </header>

  <section class="hero" role="img" aria-label="Photo of two young shoppers in a café looking at their phones">
    <div class="hero-callout">Vostrelink.com/book-demo</div>
  </section>

  <nav class="sub-nav">
    <span class="label">Learn More:</span>
    <a href="#">Our Company</a><a href="#">Testimonials</a><a href="#">Careers</a><a href="#">Help &amp; Contact</a>
    <div class="social">
      <span class="social-square"></span><span class="social-square"></span><span class="social-square"></span>
      <svg width="13" height="13" viewBox="0 0 13 13" aria-label="Search"><circle cx="5.5" cy="5.5" r="4" fill="none" stroke="#7d8a96" stroke-width="1.6"/><line x1="8.5" y1="8.5" x2="12" y2="12" stroke="#7d8a96" stroke-width="1.8"/></svg>
    </div>
  </nav>

  <section class="intro">
    <h1 class="intro-title">Delight your shoppers, impress your tenants and provide your<br>landlords with accurate detailed data in real time</h1>
    <p class="intro-sub">See some of the features below and learn why businesses trust Vostrelink</p>
    <a class="btn-demo" href="#"><svg width="9" height="10" viewBox="0 0 9 10"><path d="M0 0L9 5L0 10Z" fill="#4bbfdc"/></svg>BOOK A DEMO</a>
  </section>
</div>
</body>
</html>
```